The best Social Research house in LatinAmerica needs a Business Card

We need a greeting card that does justice to our everyday work. Marenta Civica is a group of highly selected social academic minds (6 academicians selected among 800+ candidates) that analyses the field work done by our network of 56 social anthropologists in 7 Latin American countries. We spend months studying different social phenomena or groups of people and then translate the findings into powerful insights and strategic marketing actions for our clients (from Banks to TV networks, from top worldwide consumer product Companies to Government policy design or even new product innovation initiatives). We translate social academic knowledge into tangible actions. We already have a logo and we like it, but remain open for new and different proposals on size or form. We do something very different and we need a card as different as we are.
Target Market(s)
Top Management from Top Companies that need (and like) to be surprised!
Industry/Entity Type
Marketing
Look and feel

```html
<!DOCTYPE html>
<html lang="es">
<head>
<meta charset="utf-8">
<title>Marenta Civica – Tarjeta de presentación</title>
<link rel="stylesheet" href="https://fonts.googleapis.com/css2?family=Arvo:wght@400;700&display=swap">
<style>
  :root {
    --canvas-bg: #e9e6e1;
    --card-teal: #0b917a;
    --card-teal-deep: #08846f;
    --accent-green: #6cb33f;
    --ink-white: #ffffff;
    --card-shadow: rgba(0, 0, 0, 0.18);
  }
  * { margin: 0; padding: 0; box-sizing: border-box; }
  html, body {
    width: 1200px;
    height: 900px;
    overflow: hidden;
    background: var(--canvas-bg);
    font-family: "Arvo", Georgia, serif;
    color: var(--ink-white);
  }
  .canvas {
    position: relative;
    width: 1200px;
    height: 900px;
  }
  .card {
    position: absolute;
    left: 290px;
    width: 620px;
    height: 354px;
    background: linear-gradient(135deg, var(--card-teal) 0%, var(--card-teal-deep) 100%);
    box-shadow: 0 10px 28px var(--card-shadow);
  }
  .card--front { top: 76px; }
  .card--back { top: 470px; }

  /* Front */
  .brand {
    position: absolute;
    left: 0;
    right: 0;
    top: 50%;
    transform: translateY(-50%);
    display: flex;
    align-items: center;
    justify-content: center;
    gap: 18px;
  }
  .brand__mark {
    width: 46px;
    height: 46px;
    border-radius: 50%;
    background: var(--accent-green);
  }
  .brand__name {
    font-size: 42px;
    font-weight: 700;
    color: var(--ink-white);
    letter-spacing: 0.5px;
  }

  /* Back */
  .identity {
    position: absolute;
    left: 56px;
    top: 52px;
  }
  .identity__marker {
    position: absolute;
    left: -26px;
    top: 6px;
    width: 14px;
    height: 14px;
    background: var(--accent-green);
  }
  .identity__name {
    font-size: 28px;
    font-weight: 400;
    line-height: 1.1;
  }
  .identity__role {
    font-size: 17px;
    font-weight: 400;
    margin-top: 4px;
    letter-spacing: 0.4px;
  }
  .contact-list {
    position: absolute;
    left: 38px;
    top: 182px;
    list-style: none;
  }
  .contact-list__item {
    display: flex;
    align-items: flex-start;
    gap: 14px;
    font-size: 16px;
    line-height: 1.3;
    margin-bottom: 10px;
  }
  .contact-list__icon {
    flex: none;
    width: 22px;
    height: 22px;
  }
</style>
</head>
<body>
<main class="canvas">

  <section class="card card--front" aria-label="Frente de la tarjeta">
    <div class="brand">
      <span class="brand__mark" aria-hidden="true"></span>
      <span class="brand__name">Marenta Civica</span>
    </div>
  </section>

  <section class="card card--back" aria-label="Reverso de la tarjeta">
    <div class="identity">
      <span class="identity__marker" aria-hidden="true"></span>
      <h1 class="identity__name">Tomas Ledesma</h1>
      <p class="identity__role">Gabinete de Análisis</p>
    </div>

    <ul class="contact-list">
      <li class="contact-list__item">
        <svg class="contact-list__icon" viewBox="0 0 22 22" aria-hidden="true">
          <circle cx="11" cy="11" r="11" fill="#6cb33f"/>
          <path d="M7.5 6.2c.5-.4 1.1-.3 1.4.2l1 1.6c.3.4.2 1-.2 1.3l-.6.5c.5 1.2 1.4 2.1 2.6 2.6l.5-.6c.3-.4.9-.5 1.3-.2l1.6 1c.5.3.6.9.2 1.4l-.7.8c-.5.5-1.3.7-2 .4-2.6-1-4.6-3-5.6-5.6-.3-.7-.1-1.5.4-2z" fill="#fff"/>
        </svg>
        <span>(55) 5550 1234</span>
      </li>
      <li class="contact-list__item">
        <svg class="contact-list__icon" viewBox="0 0 22 22" aria-hidden="true">
          <circle cx="11" cy="11" r="11" fill="#6cb33f"/>
          <rect x="5.5" y="7" width="11" height="8" fill="#fff"/>
          <path d="M5.5 7l5.5 4.5L16.5 7" fill="none" stroke="#6cb33f" stroke-width="1.2"/>
        </svg>
        <span>tomas.ledesma@marenta-civica.com</span>
      </li>
      <li class="contact-list__item">
        <svg class="contact-list__icon" viewBox="0 0 22 22" aria-hidden="true">
          <circle cx="11" cy="11" r="11" fill="#6cb33f"/>
          <path d="M11 4.5a4 4 0 0 0-4 4c0 3 4 8 4 8s4-5 4-8a4 4 0 0 0-4-4z" fill="#fff"/>
          <circle cx="11" cy="8.6" r="1.5" fill="#6cb33f"/>
        </svg>
        <span>Calle Olmo 14. Col. Roma<br>Mexico DF 06700. MX.</span>
      </li>
    </ul>
  </section>

</main>
</body>
</html>
```